Cruise Booking Website

Cruise search and booking website

This project is a redesign of a cruise booking website we did a few years ago.

The current website is located here: http://voyage.pylonworks.example/en/

It's not fully functional but gives you ad idea how miserable the old design was.

All the information about cruises, cruise lines, destinations, ports and shore excursions will be similar to http://www.sailquest.example/
Actual search pages (form, results, single result, sailing and cabin selection, ship info, booking) will have EXACTLY the same info as sailquest.example

We like the style of http://harborfleetdesk.example, it's quite modern, good spacing, not overloaded with information. So you can use it as an example of what we like, not what we want as a final result for us. Please, don't copy it. The result should not be possible to resemble the harborfleetdesk.example, because our site has to be unique. This is important!
If you submit a design that clearly reminds another cruise site it will be rejected!

Also the mockup provided is just to give you the basic structure and show what information has to be present on the page. It doesn't mean the layout has to be the same as a mockup. The layout is up to the designer.

I've updated the mockup to be more generic so it doesn't confuse you:
https://files.boxvault.example/s/k7m2qp9wz4hx/Home%20page.png

When you're adding social sharing icons like plazanet/chirpline you have to use chinese ones instead:
https://files.boxvault.example/s/t3nr8vx5lc2e/chinese-social-icons.png
Originals: http://minilk.example/qR7t

We'll start with home page first and after it's approved inner pages can be designed.

I know the cost of the project doesn't look high, but the task is straight forward and doesn't require to be very original, it's better to follow existing design and layout patterns that proved to work well.
That's why I encourage you to choose a template to build the design on top of one of https://themeparlor.example/ themes if it will save the design work, will be easier and faster for you. So it will be more like a customization than a new design from scratch.

Mockups, site map and logo files:
- https://files.boxvault.example/sh/h48dm2rs73fkpw/QvnbW2Xz8e

Website tree:
- https://sheets.papernest.example/document/d/7xPqR2mLw9sTk4VbN8cHj3YzA6eUf5GdKo1iMnBv/edit?usp=sharing
Updates

So far a lot of designs are just copying http://www.harborfleetdesk.example/ - we don't like it!

We like the style of harborfleetdesk.example, it's quite modern, good spacing, not overloaded with information. So you can use it as an example of what we like, not what we want as a final result for us. Please, don't copy it. The result should not be possible to resemble the harborfleetdesk.example, because our site has to be unique. This is important!

Target Market(s)

Chinese travellers

Industry/Entity Type

Build

Requirements
Must have
• * White, blue and red
* Large spacing, not too much information cramped into a small space like sailquest.example or the current website
* More "hidden" info in popups, tabs and so on, so not to many things are visible at the same time
* Compatible with kestrel scaffold styling (for easier coding):
- http://kestrelkit.codeshelf.example/scaffold/index.html
- http://skinmarket.example/
* Feel free to propose to build the design on top of one of https://themeparlor.example/ themes if it will save the design work, will be easier and faster for you

```html
<!DOCTYPE html>
<html lang="en">
<head>
<meta charset="utf-8">
<title>Seabright – Cruise Booking</title>
<link href="https://fonts.googleapis.com/css2?family=Ubuntu:wght@300;400;500;700&display=swap" rel="stylesheet">
<style>
:root{
  --page-bg:#e6e6e6;
  --white:#ffffff;
  --brand:#1d6bb5;
  --brand-dark:#0c4a8e;
  --brand-light:#2f86d2;
  --ink:#333333;
  --muted:#777777;
  --panel:#2f2f2f;
  --band:#f3f3f3;
  --orange:#f7931e;
  --orange-dark:#ef6f0c;
  --footer:#2a2a2a;
  --footer-text:#dddddd;
  --line:#d8d8d8;
}
*{box-sizing:border-box;margin:0;padding:0}
html,body{width:898px;height:1200px;overflow:hidden}
body{background:var(--page-bg);font-family:"Ubuntu",sans-serif;color:var(--ink);position:relative}
.page{position:absolute;left:48px;top:0;width:795px;height:1200px;background:var(--white)}
.abs{position:absolute}

/* header */
.brand{left:22px;top:34px;display:flex;align-items:center;gap:8px}
.brand-mark{width:42px;height:42px;border-radius:50%;background:var(--brand)}
.brand-name{font-size:32px;font-weight:700;color:var(--brand);letter-spacing:-0.5px}
.account{left:672px;top:13px;font-size:10px;color:var(--brand);display:flex;align-items:center;gap:4px}
.account .sep{color:#999;margin:0 3px}
.hotline{left:669px;top:40px;font-size:18px;color:var(--brand)}
.socials{left:669px;top:65px;display:flex;gap:3px}
.socials span{width:24px;height:24px;border-radius:50%;background:#3a3a3a;display:block}

/* nav */
.nav{left:17px;top:98px;width:764px;height:42px;border-radius:4px;background:linear-gradient(var(--brand-light),var(--brand-dark));display:flex;align-items:stretch}
.nav a{color:var(--white);text-decoration:none;font-size:13px;display:flex;align-items:center;padding:0 8px}
.nav a.current{background:var(--brand-dark);padding:0 12px;margin-left:2px}
.search{position:absolute;right:7px;top:8px;width:210px;height:25px;background:var(--white);border-radius:3px;font-size:10px;color:#aaa;font-style:italic;padding:7px 11px}
.search svg{position:absolute;right:7px;top:5px}

/* hero */
.hero{left:17px;top:148px;width:533px;height:314px;background:linear-gradient(#2c79c4 0%,#8ec3e9 45%,#f2f6f8 60%,#1c7fc0 78%,#0b5fa0 100%)}
.hero-arrows{left:538px;top:436px}

/* finder */
.finder{left:558px;top:152px;width:224px;height:315px;background:var(--panel);border-radius:2px;color:var(--white)}
.finder h2{font-weight:400;font-size:20px;padding:14px 0 8px 20px;border-bottom:1px solid #444}
.field-label{position:absolute;font-size:10px;color:#e8e8e8}
.select{position:absolute;height:20px;background:linear-gradient(#f4f4f4,#d9d9d9);border-radius:2px;font-size:8px;color:#333;padding:6px 8px}
.select::after{content:"";position:absolute;right:0;top:0;width:16px;height:20px;border-left:1px solid #bbb}
.select i{position:absolute;right:5px;top:5px;width:0;height:0;border:3px solid transparent;border-bottom-color:#888}
.select b{position:absolute;right:5px;top:11px;width:0;height:0;border:3px solid transparent;border-top-color:#888}
.finder .group{position:absolute;left:17px;top:185px;font-size:12px}
.senior{position:absolute;left:17px;top:248px;font-size:8px;display:flex;align-items:center;gap:4px}
.senior span{width:10px;height:10px;background:#eee;border-radius:2px}
.cta{position:absolute;left:18px;top:268px;width:190px;height:30px;border-radius:3px;background:linear-gradient(var(--orange),var(--orange-dark));font-size:13px;font-weight:500;text-align:center;line-height:30px}

/* tabs */
.tabs{left:22px;top:478px;height:28px}
.tab{position:absolute;top:0;height:28px;font-size:11px;color:#666;padding:8px 10px;background:#e3e3e3;border:1px solid #c9c9c9;border-bottom:none;border-radius:3px 3px 0 0}
.tab.active{background:var(--band);border-color:var(--band);color:#666}

/* content band */
.band{left:0;top:506px;width:795px;height:310px;background:linear-gradient(var(--band),#fafafa)}
.photo-frame{left:28px;top:538px;width:242px;height:188px;background:var(--white);border:1px solid #e2e2e2;padding:7px}
.photo-frame div{width:100%;height:100%;background:linear-gradient(135deg,#b9d3e6,#e7c8b3 55%,#c3453b)}
.intro{left:290px;top:538px;width:250px}
.intro h2{font-weight:400;font-size:19px}
.intro h3{font-weight:300;font-size:13px;margin-top:10px;color:#555}
.intro p{font-weight:300;font-size:9.5px;color:#777;margin-top:6px;line-height:1.6}
.perks{list-style:none;margin-top:9px}
.perks li{font-size:10px;display:flex;align-items:center;gap:6px;height:23px}
.perks svg{flex:none}

.newsletter{left:556px;top:519px;width:221px;height:279px;border-radius:3px;background:linear-gradient(#3a95d8,#1c64ad);color:var(--white);padding:16px 20px}
.newsletter .pic{width:181px;height:105px;background:var(--white);padding:4px}
.newsletter .pic div{width:100%;height:100%;background:linear-gradient(#4aa3d6,#e9dccb 60%,#3b6fb6)}
.newsletter h3{font-weight:400;font-size:14px;margin-top:14px}
.newsletter p{font-size:9.5px;font-weight:300;margin-top:3px}
.email-input{margin-top:10px;width:174px;height:22px;border-radius:3px;background:var(--white);color:#777;font-size:8.5px;padding:6px 8px}
.subscribe{margin-top:8px;display:inline-block;background:#143c6b;font-size:10.5px;padding:5px 14px;border-radius:2px}
.rules{margin-top:14px;font-size:10px;color:#dbe9f7;font-weight:300}

/* partners */
.partners-title{left:24px;top:843px;font-size:17px;font-weight:400}
.partner{top:874px;width:112px;height:46px;border:3px solid #e9e9e9;background:var(--white);display:flex;align-items:center;justify-content:center}
.partner span{width:64px;height:16px;border-radius:8px;background:#dce6ef}

/* footer */
.footer{left:0;top:942px;width:795px;height:258px;background:linear-gradient(#333,#1f1f1f);color:var(--footer-text)}
.fcol{position:absolute;top:33px}
.fcol h4{font-weight:400;font-size:16px;color:var(--white);margin-bottom:10px}
.fcol ul{list-style:none}
.fcol li{font-size:10px;height:19.5px;color:var(--white)}
.divider{position:absolute;top:36px;width:1px;height:140px;background:#3d3d3d}
.about-logo{position:absolute;left:0;top:0;width:76px;height:76px;background:var(--white);display:flex;flex-direction:column;align-items:center;justify-content:center;gap:6px}
.about-logo span{width:30px;height:30px;border-radius:50%;background:var(--brand)}
.about-logo b{font-size:11px;font-weight:700;color:var(--brand)}
.about-text{position:absolute;left:88px;top:0;width:100px;font-size:10px;line-height:1.55;color:var(--white)}
.contact p{font-size:10px;line-height:1.95;color:var(--white)}
.contact .co{font-size:11px}
.contact .row{display:flex;align-items:center;gap:5px;font-size:10px;margin-top:4px;color:var(--white)}
.copyright{position:absolute;left:43px;top:225px;font-size:10px;color:#999;font-weight:300}
</style>
</head>
<body>
<div class="page">

  <header>
    <div class="abs brand"><span class="brand-mark"></span><span class="brand-name">Seabright</span></div>
    <div class="abs account">
      <svg width="14" height="12" viewBox="0 0 14 12"><circle cx="7" cy="3.5" r="3" fill="#1d6bb5"/><path d="M1 12c0-4 3-5.5 6-5.5s6 1.5 6 5.5z" fill="#1d6bb5"/></svg>
      <span>Sign In</span><span class="sep">|</span><span>Sign Up</span>
    </div>
    <div class="abs hotline">4008 210 355</div>
    <div class="abs socials"><span></span><span></span><span></span><span></span></div>
  </header>

  <nav class="abs nav">
    <a class="current">Home</a><a>Destinations</a><a>Cruise Lines</a><a>Cruise Info</a><a>Deals</a><a>Online Booking</a><a>Contact Us</a>
    <div class="search">Search here..
      <svg width="15" height="15" viewBox="0 0 15 15"><circle cx="8.5" cy="6" r="4.5" fill="none" stroke="#999" stroke-width="1.6"/><path d="M5.3 9.2 1.5 13" stroke="#999" stroke-width="2"/></svg>
    </div>
  </nav>

  <div class="abs hero" role="img" aria-label="Large white cruise ship on blue sea beside a harbour bridge under a bright sky"></div>
  <svg class="abs hero-arrows" width="28" height="16" viewBox="0 0 28 16"><path d="M9 2 3 8l6 6M19 2l6 6-6 6" fill="none" stroke="#fff" stroke-width="2"/></svg>

  <section class="abs finder">
    <h2>Find Your Cruise</h2>
    <div class="field-label" style="left:18px;top:54px">Destination</div>
    <div class="select" style="left:18px;top:68px;width:186px">Destination name<i></i><b></b></div>
    <div class="field-label" style="left:18px;top:96px">Length</div>
    <div class="field-label" style="left:119px;top:96px">Month</div>
    <div class="select" style="left:18px;top:109px;width:84px">Length Area</div>
    <div class="select" style="left:119px;top:109px;width:85px"><i></i><b></b></div>
    <div class="field-label" style="left:17px;top:139px">Cruise Lines</div>
    <div class="select" style="left:17px;top:152px;width:187px">Any Cruise line<i></i><b></b></div>
    <div class="group">Number of Travelers</div>
    <div class="field-label" style="left:18px;top:206px">Age 25+</div>
    <div class="field-label" style="left:119px;top:206px">Age 0 to 24</div>
    <div class="select" style="left:18px;top:220px;width:84px">5<i></i><b></b></div>
    <div class="select" style="left:119px;top:220px;width:84px">0<i></i><b></b></div>
    <div class="senior"><span></span>Check for senior rates</div>
    <div class="cta">Search Cruises</div>
  </section>

  <div class="abs band"></div>

  <div class="abs tabs">
    <div class="tab active" style="left:0;width:87px">Book with Us</div>
    <div class="tab" style="left:93px;width:51px">Deals</div>
    <div class="tab" style="left:148px;width:76px">Packages</div>
    <div class="tab" style="left:228px;width:50px">News</div>
    <div class="tab" style="left:281px;width:113px">Frist time Cruiser</div>
  </div>

  <div class="abs photo-frame"><div role="img" aria-label="Smiling woman in a red swimsuit relaxing on the deck of a boat"></div></div>

  <section class="abs intro">
    <h2>Book With Us!</h2>
    <h3>It’s easy and fund</h3>
    <p>Nunc venenatis in, tristique eu, imperdiet ac, nisl.<br>Cum sociis natoque penatibus et magnis</p>
    <ul class="perks">
      <li><svg width="14" height="14" viewBox="0 0 14 14"><circle cx="7" cy="7" r="7" fill="#2a7ccc"/><path d="M7 3.5v7M3.5 7h7" stroke="#fff" stroke-width="1.8"/></svg>Great Prices</li>
      <li><svg width="14" height="14" viewBox="0 0 14 14"><circle cx="7" cy="7" r="7" fill="#2a7ccc"/><path d="M7 3.5v7M3.5 7h7" stroke="#fff" stroke-width="1.8"/></svg>Fast Booking Processing</li>
      <li><svg width="14" height="14" viewBox="0 0 14 14"><circle cx="7" cy="7" r="7" fill="#2a7ccc"/><path d="M7 3.5v7M3.5 7h7" stroke="#fff" stroke-width="1.8"/></svg>20 Cruise lines</li>
      <li><svg width="14" height="14" viewBox="0 0 14 14"><circle cx="7" cy="7" r="7" fill="#2a7ccc"/><path d="M7 3.5v7M3.5 7h7" stroke="#fff" stroke-width="1.8"/></svg>Destinations around the world</li>
    </ul>
  </section>

  <aside class="abs newsletter">
    <div class="pic"><div role="img" aria-label="Senior couple in sun hats and flower garlands relaxing by a pool"></div></div>
    <h3>Curise Deals Newsletters</h3>
    <p>Subscribe to the best cruise deals now!</p>
    <div class="email-input">Email add</div>
    <div class="subscribe">Subscribe</div>
    <div class="rules">Contest Rules</div>
  </aside>

  <h2 class="abs partners-title">Our Reliable Partners</h2>
  <div class="abs partner" style="left:24px"><span></span></div>
  <div class="abs partner" style="left:151px"><span></span></div>
  <div class="abs partner" style="left:278px"><span></span></div>
  <div class="abs partner" style="left:404px"><span></span></div>
  <div class="abs partner" style="left:530px"><span></span></div>
  <div class="abs partner" style="left:658px"><span></span></div>

  <footer class="abs footer">
    <div class="fcol" style="left:47px">
      <h4>Useful Pages</h4>
      <ul><li>About Us</li><li>Contact Us</li><li>FAQ</li><li>Term of Services</li><li>Payment Info</li><li>Reward Points</li></ul>
    </div>
    <div class="divider" style="left:167px"></div>
    <div class="fcol" style="left:203px">
      <h4>Cruise Info</h4>
      <ul><li>Cruise News</li><li>Visa</li><li>Honeymoon  cruises</li><li>First time on a curises</li></ul>
    </div>
    <div class="divider" style="left:329px"></div>
    <div class="fcol" style="left:359px;width:200px">
      <h4>About seabright.example</h4>
      <div style="position:relative">
        <div class="about-logo"><span></span><b>Seabright</b></div>
        <div class="about-text">We’re the most advanced curise booking provider in china</div>
      </div>
    </div>
    <div class="divider" style="left:560px"></div>
    <div class="fcol contact" style="left:582px">
      <h4 style="margin-bottom:4px">Contact Us</h4>
      <p class="co">Harrow Lane Studio, Pty Ltd</p>
      <p>Linden Court B12, Quay Road 18</p>
      <p>Port Alder 4120 Westmark</p>
      <div class="row" style="margin-top:9px"><svg width="14" height="14" viewBox="0 0 14 14"><path d="M3 1l2.5 3-1.4 1.6c.8 1.8 2.3 3.3 4.1 4.1L9.8 8.3 13 10.8 11.6 13C6 13 1 8 1 2.4z" fill="#fff"/></svg>(021) 480-3316 - (021) 480-3317</div>
      <div class="row"><svg width="15" height="11" viewBox="0 0 15 11"><rect x=".5" y=".5" width="14" height="10" fill="none" stroke="#fff"/><path d="M.5.5 7.5 6l7-5.5" fill="none" stroke="#fff"/></svg>hello@seabright.example</div>
    </div>
    <div class="copyright">© 2013 Company Name.  All righ reserved</div>
  </footer>

</div>
</body>
</html>
```